business card - Helicopter Flight Services, Flight School, etc.

We need a business card design for a new helicopter service.

We offer Helicopter Flight Services, Aerial Filming & Photography, Flight School, and Helicopter Tours. In that order.

Summit BladeAir, Inc.
Dennis Tollerby
SummitBladeair@Kestmail.com
626-418-7352

Based at the Brenwick Airport in Van Nuys, CA. The final design should communicate integrity and safety. Pictures or logos at your discretion.

Card back side - surprise me.

```html
<!DOCTYPE html>
<html lang="en">
<head>
<meta charset="utf-8">
<title>Summit BladeAir, Inc. — Business Card</title>
<link href="https://fonts.googleapis.com/css2?family=Open+Sans:wght@300;400&display=swap" rel="stylesheet">
<style>
  :root {
    --backdrop: #e6e4e1;
    --card: #141414;
    --ink: #ffffff;
    --muted: #d9d9d9;
  }
  * { margin: 0; padding: 0; box-sizing: border-box; }
  html, body {
    width: 1200px; height: 780px; overflow: hidden;
    background: var(--backdrop);
    font-family: "Open Sans", sans-serif;
  }
  .stage { position: relative; width: 1200px; height: 780px; }
  .card {
    position: absolute; top: 240px;
    width: 525px; height: 300px;
    background: var(--card); color: var(--ink);
    overflow: hidden;
    box-shadow: 0 10px 26px rgba(0,0,0,.28);
  }
  .card--front { left: 50px; }
  .card--back { left: 625px; }

  .frame {
    position: absolute; left: 40px; top: 28px; width: 445px; height: 185px;
    border: 2px solid var(--ink); border-bottom: none;
  }
  .frame__foot {
    position: absolute; bottom: 0; height: 2px; background: var(--ink);
  }
  .frame__foot--left { left: -2px; width: 140px; }
  .frame__foot--right { right: -2px; width: 145px; }

  .stripe {
    position: absolute; left: 0; top: 232px; width: 440px; height: 32px;
    background: var(--ink);
  }

  .front__title {
    position: absolute; left: 60px; top: 58px;
    font-size: 37px; font-weight: 300; letter-spacing: -0.5px; white-space: nowrap;
  }
  .front__services {
    position: absolute; left: 40px; top: 116px; width: 445px;
    text-align: center; list-style: none;
    font-size: 13.5px; font-weight: 300; line-height: 21px; color: var(--muted);
  }
  .front__services li { white-space: nowrap; }

  .back__title {
    position: absolute; left: 95px; top: 36px;
    font-size: 34px; font-weight: 300; letter-spacing: -0.5px; white-space: nowrap;
  }
  .back__rule {
    position: absolute; left: 60px; top: 92px; width: 410px; height: 2px; background: var(--ink);
  }
  .back__name {
    position: absolute; left: 62px; top: 130px;
    font-size: 16px; font-weight: 300; color: var(--muted); white-space: nowrap;
  }
  .back__divider {
    position: absolute; left: 262px; top: 118px; width: 2px; height: 80px; background: var(--ink);
  }
  .contact {
    position: absolute; left: 275px; top: 122px; list-style: none;
    font-size: 11.5px; font-weight: 400; line-height: 16px; color: var(--muted);
  }
  .contact li { display: flex; align-items: flex-start; gap: 6px; white-space: nowrap; }
  .contact svg { flex: none; margin-top: 3px; }
  .contact__spacer { width: 10px; flex: none; }
</style>
</head>
<body>
<main class="stage">

  <section class="card card--front" aria-label="Business card front">
    <div class="frame">
      <span class="frame__foot frame__foot--left"></span>
      <span class="frame__foot frame__foot--right"></span>
    </div>
    <h1 class="front__title">Summit BladeAir, Inc.</h1>
    <ul class="front__services">
      <li>Helicopter Flight Services · Aerial Filming &amp; Photography</li>
      <li>Flight School · Helicopter Tours</li>
    </ul>
    <div class="stripe"></div>
  </section>

  <section class="card card--back" aria-label="Business card back">
    <div class="frame">
      <span class="frame__foot frame__foot--left"></span>
      <span class="frame__foot frame__foot--right"></span>
    </div>
    <h2 class="back__title">Summit BladeAir, Inc.</h2>
    <div class="back__rule"></div>
    <p class="back__name">Dennis Tollerby</p>
    <div class="back__divider"></div>
    <ul class="contact">
      <li>
        <svg width="10" height="10" viewBox="0 0 10 10" aria-hidden="true">
          <rect width="10" height="10" fill="#fff"/>
          <path d="M3 2 L4.2 3.6 L3.6 4.4 Q4.6 6 5.8 6.6 L6.6 6 L8 7.2 L7.2 8.2 Q4.2 7.6 2.2 3 Z" fill="#141414"/>
        </svg>
        <span>626-418-7352</span>
      </li>
      <li>
        <svg width="10" height="10" viewBox="0 0 10 10" aria-hidden="true">
          <rect width="10" height="10" fill="#fff"/>
          <rect x="2" y="3" width="6" height="4.2" fill="none" stroke="#141414" stroke-width="0.9"/>
          <path d="M2 3 L5 5.4 L8 3" fill="none" stroke="#141414" stroke-width="0.9"/>
        </svg>
        <span>SummitBladeair@Kestmail.com</span>
      </li>
      <li>
        <svg width="10" height="10" viewBox="0 0 10 10" aria-hidden="true">
          <rect width="10" height="10" fill="#fff"/>
          <path d="M5 8.4 L3 5 A2.3 2.3 0 1 1 7 5 Z" fill="#141414"/>
          <circle cx="5" cy="4" r="0.8" fill="#fff"/>
        </svg>
        <span>Brenwick Airport, Hangar A</span>
      </li>
      <li>
        <span class="contact__spacer"></span>
        <span>Van Nuys, CA 91406</span>
      </li>
    </ul>
    <div class="stripe"></div>
  </section>

</main>
</body>
</html>
```